Post storm repair flyer

looking for an eye catching 6x9 postcard to send out to single family home owners advertising a "Post Storm Repair Special" explaining that after the recent hurricanes its very important to have your roof checked and any repairs fixed right away before they become a bigger more costly problem and that even though your home wasn't directly hit by the storm the high wind gust could've cause unseen damage.
offer $200 off any repair *some rules may apply
Crest Roofing
877.512.DUNE
www.DuneRoofingco.example

```html
<!DOCTYPE html>
<html lang="en">
<head>
<meta charset="utf-8">
<title>Crest Roofing – Post Storm Repair Special Postcard</title>
<link rel="stylesheet" href="https://fonts.googleapis.com/css2?family=Outfit:wght@400;500;600;700;800&display=swap">
<style>
  :root{
    --charcoal:#2b2a29;
    --honey:#e6b335;
    --stage:#737373;
    --paper:#ffffff;
    --stamp:#d6d6d6;
    --rule:#8a8a8a;
    --shingle-a:#9c8676;
    --shingle-b:#5f5853;
    --sky:#5d8fd1;
    --grass:#6f8f3e;
  }
  *{box-sizing:border-box;margin:0;padding:0}
  html,body{width:1200px;height:2283px;overflow:hidden}
  body{background:var(--stage);font-family:"Outfit",Arial,sans-serif;position:relative}
  .postcard{position:absolute;left:137px;width:926px;height:616px;background:var(--paper);overflow:hidden}
  .postcard--front{top:475px}
  .postcard--back{top:1191px}
  .postcard__art{position:absolute;inset:0;width:926px;height:616px}
  .txt{position:absolute;line-height:1;white-space:nowrap}

  /* front */
  .headline{left:44px;color:var(--paper);font-size:60px;font-weight:500;letter-spacing:-.5px}
  .headline--top{top:60px}
  .headline--bold{top:116px;font-size:57px;font-weight:700}
  .intro{position:absolute;left:44px;top:182px;color:var(--paper);font-size:16px;line-height:20px;width:315px}
  .offer__amount{left:40px;top:284px;font-size:120px;font-weight:800;color:var(--charcoal);letter-spacing:-5px}
  .offer__off{left:277px;top:327px;font-size:23px;font-weight:700;color:var(--paper)}
  .offer__label{left:86px;top:387px;font-size:35px;font-weight:700;color:var(--charcoal)}
  .offer__terms{left:174px;top:426px;font-size:11px;color:var(--charcoal)}
  .cta-tag{color:var(--paper);font-size:19px;font-weight:500;letter-spacing:.3px}
  .phone{font-size:50px;font-weight:700;color:var(--charcoal);letter-spacing:-.5px}
  .web{font-size:23px;font-weight:600;color:var(--charcoal)}
  .brand-name{font-size:22px;font-weight:500;color:var(--charcoal);letter-spacing:.3px}

  /* back */
  .services__title{left:46px;top:34px;font-size:56px;font-weight:700;color:var(--paper)}
  .services__list{position:absolute;left:46px;top:98px;list-style:none}
  .services__item{position:relative;padding-left:25px;color:var(--paper);font-size:19px;font-weight:700;line-height:20px;margin-bottom:21px;text-transform:uppercase}
  .services__item svg{position:absolute;left:0;top:1px;width:18px;height:18px}
  .process__kicker{left:46px;top:323px;font-size:30px;font-weight:500;color:var(--charcoal)}
  .process__title{left:44px;top:350px;font-size:54px;font-weight:700;color:var(--charcoal)}
  .steps{position:absolute;left:46px;top:413px;list-style:none}
  .step{display:flex;align-items:flex-start;height:64px}
  .step__num{width:36px;height:36px;background:var(--charcoal);color:var(--paper);font-size:20px;font-weight:600;display:flex;align-items:center;justify-content:center;margin-right:11px;flex:none}
  .step__text{font-size:15px;line-height:19px;color:var(--charcoal)}
</style>
</head>
<body>

<!-- FRONT -->
<section class="postcard postcard--front" aria-label="Postcard front">
  <svg class="postcard__art" viewBox="0 0 926 616">
    <defs>
      <linearGradient id="roofTone" x1="0" y1="0" x2="1" y2="1">
        <stop offset="0" stop-color="#9c8676"/>
        <stop offset="1" stop-color="#5f5853"/>
      </linearGradient>
      <linearGradient id="houseTone" x1="0" y1="0" x2="0" y2="1">
        <stop offset="0" stop-color="#5d8fd1"/>
        <stop offset=".55" stop-color="#c9cfd6"/>
        <stop offset="1" stop-color="#6f8f3e"/>
      </linearGradient>
    </defs>
    <polygon role="img" aria-label="Photo of a storm-damaged shingle roof with torn shingles" points="451,0 926,0 926,436 600,436 590,616 566,616 486,271" fill="url(#roofTone)"/>
    <polygon points="0,0 451,0 486,271 0,271" fill="#2b2a29"/>
    <polygon points="0,271 486,271 350,450 0,450" fill="#e6b335"/>
    <polygon points="398,185 420,197.5 420,222.5 398,235 376,222.5 376,197.5" fill="#e6b335"/>
    <polygon points="491,192 638,277 638,443 491,528 344,443 344,277" fill="#ffffff"/>
    <polygon role="img" aria-label="Photo of a house with its roof torn off by a hurricane" points="491,204 628,283 628,437 491,516 354,437 354,283" fill="url(#houseTone)"/>
    <polygon points="403,470 425,482.5 425,507.5 403,520 381,507.5 381,482.5" fill="#6b6b6b"/>
    <polygon points="441,512 476,532 476,572 441,592 406,572 406,532" fill="none" stroke="#e6b335" stroke-width="6"/>
    <polygon points="44,471 258,471 271,498 44,498" fill="#2b2a29"/>
  </svg>
  <h1 class="txt headline headline--top">POST STORM</h1>
  <h1 class="txt headline headline--bold">REPAIR SPECIAL</h1>
  <p class="intro">Recent hurricane winds can leave unseen roof damage, even if your home wasn't hit. Fix it now before it gets costly.</p>
  <div class="txt offer__amount">$200</div>
  <div class="txt offer__off">OFF</div>
  <div class="txt offer__label">ANY REPAIR*</div>
  <div class="txt offer__terms">*some rules may apply</div>
  <div class="txt cta-tag" style="left:52px;top:475px">Request Consultation</div>
  <div class="txt phone" style="left:42px;top:508px">877.512.DUNE</div>
  <div class="txt web" style="left:44px;top:568px">www.DuneRoofingco.example</div>
  <div class="txt brand-name" style="left:690px;top:575px">CREST ROOFING</div>
</section>

<!-- BACK -->
<section class="postcard postcard--back" aria-label="Postcard back">
  <svg class="postcard__art" viewBox="0 0 926 616">
    <defs>
      <linearGradient id="crewTone" x1="0" y1="0" x2="0" y2="1">
        <stop offset="0" stop-color="#b9c9d8"/>
        <stop offset=".3" stop-color="#6a6c70"/>
        <stop offset="1" stop-color="#3f4144"/>
      </linearGradient>
    </defs>
    <polygon points="0,0 416,0 442,135 316,195 316,300 0,300" fill="#2b2a29"/>
    <polygon points="436,128 556,196 556,339 436,407 316,339 316,196" fill="#ffffff"/>
    <polygon role="img" aria-label="Photo of a roofing crew installing shingles on a roof" points="436,140 546,203 546,332 436,395 326,332 326,203" fill="url(#crewTone)"/>
    <rect x="814" y="30" width="83" height="83" fill="#d6d6d6"/>
    <line x1="582" y1="307" x2="855" y2="307" stroke="#8a8a8a" stroke-width="1"/>
    <line x1="582" y1="370" x2="855" y2="370" stroke="#8a8a8a" stroke-width="1"/>
    <line x1="582" y1="433" x2="855" y2="433" stroke="#8a8a8a" stroke-width="1"/>
    <polygon points="482,378 496,378 550,616 536,616" fill="#2b2a29"/>
    <polygon points="521,482 748,482 761,510 521,510" fill="#2b2a29"/>
  </svg>
  <h2 class="txt services__title">SERVICES</h2>
  <ul class="services__list">
    <li class="services__item"><svg viewBox="0 0 18 18"><circle cx="9" cy="9" r="9" fill="#fff"/><path d="M5 9.3l2.7 2.6L13 6.5" fill="none" stroke="#2b2a29" stroke-width="2.2"/></svg>Retail/Commercial<br>Roof Replacement</li>
    <li class="services__item"><svg viewBox="0 0 18 18"><circle cx="9" cy="9" r="9" fill="#fff"/><path d="M5 9.3l2.7 2.6L13 6.5" fill="none" stroke="#2b2a29" stroke-width="2.2"/></svg>Storm Damage Roof<br>Replacement</li>
    <li class="services__item"><svg viewBox="0 0 18 18"><circle cx="9" cy="9" r="9" fill="#fff"/><path d="M5 9.3l2.7 2.6L13 6.5" fill="none" stroke="#2b2a29" stroke-width="2.2"/></svg>Repairs &amp; Restoration</li>
    <li class="services__item"><svg viewBox="0 0 18 18"><circle cx="9" cy="9" r="9" fill="#fff"/><path d="M5 9.3l2.7 2.6L13 6.5" fill="none" stroke="#2b2a29" stroke-width="2.2"/></svg>New Construction</li>
  </ul>
  <div class="txt process__kicker">CREST ROOFING</div>
  <h2 class="txt process__title">PROCESS</h2>
  <ol class="steps">
    <li class="step"><span class="step__num">01</span><span class="step__text">Complimentary consultation to access your roofing<br>needs and review our honest recommendations.</span></li>
    <li class="step"><span class="step__num">02</span><span class="step__text">Our team of professionals replace, restore, or repair<br>your roof making the process as stress-free as possible.</span></li>
    <li class="step"><span class="step__num">03</span><span class="step__text">100% satisfaction, peace of mind, and continued<br>professional coverage backed by CREST Protection*.</span></li>
  </ol>
  <div class="txt brand-name" style="left:494px;top:123px;font-size:21px">CREST ROOFING</div>
  <div class="txt cta-tag" style="left:531px;top:486px">Request Consultation</div>
  <div class="txt phone" style="left:544px;top:520px">877.512.DUNE</div>
  <div class="txt web" style="left:560px;top:574px">www.duneroofingco.example</div>
</section>

</body>
</html>
```